Sticker to put on shipping boxes-Pet ProductDelivery

I am looking for a sticker to put on the exterior of brown shipping boxes. We deliver pet products to a local consumer base and if our clients are not home, we leave the products on the door step. We would like to place a sticker on the box so that when looking at the box the consumer knows it came from us.

Looking for a design that is not larger than about a 3x5 or 5x5? I want it large enough to stand out, yet not so large that it is overwhelming. It also does not have to be square. It can also be rectangle. It will be placed in a bottom corner.

The design need to stand out on a brown box.

Attached is our logo for you to play around with.

Take note that the file with our slogan has colors mixes up.

The words 'Premium Pet Products' should be the same gray and the word 'Pet'. And the word 'Delivered' the same color as the word 'Brisk'.

Target Market(s)

Audience is mid 20's to seniors in senior living complexes. Those interested in convince and too buy to shop for themselves.

Industry/Entity Type

Shipping

Requirements
Must have
• Color but not overwhelming.

Orange, green, blue to match the logo colors.
Should not have
• Does not need to have a lot of text. Focus more on the Brisk Paw name and logo.

```html
<!DOCTYPE html>
<html lang="en">
<head>
<meta charset="utf-8">
<title>Brisk Paw – Delivered Sticker Options</title>
<link rel="stylesheet" href="https://fonts.googleapis.com/css2?family=Open+Sans:ital,wght@0,400;0,600;1,600;1,800&display=swap">
<style>
  :root {
    --kraft: #c9a27c;
    --white: #ffffff;
    --ink-grey: #6d6e71;
    --light-grey: #a7a9ac;
    --frame-grey: #b1b1b6;
    --band-grey: #adadb2;
    --brand-blue: #35a8e0;
    --brand-blue-deep: #2f8fd0;
    --brand-green: #8dc63f;
    --brand-orange: #f7941d;
    --dark-line: #666769;
  }
  * { box-sizing: border-box; margin: 0; padding: 0; }
  html, body { width: 1200px; height: 1000px; overflow: hidden; }
  body {
    background: var(--kraft);
    font-family: "Open Sans", Arial, sans-serif;
    position: relative;
  }

  .sticker {
    position: absolute;
    display: flex;
  }
  .sticker__face {
    flex: 1;
    background: var(--white);
    display: flex;
    flex-direction: column;
    overflow: hidden;
  }
  .brand {
    flex: 1;
    display: flex;
    flex-direction: column;
    align-items: center;
    justify-content: center;
    gap: 8px;
    padding-top: 20px;
  }
  .brand__mark {
    display: flex;
    align-items: center;
    gap: 10px;
  }
  .brand__dot {
    width: 18px; height: 18px;
    border-radius: 50%;
    background: var(--brand-orange);
  }
  .brand__name {
    font-size: 44px;
    font-weight: 400;
    color: var(--ink-grey);
    letter-spacing: -0.5px;
    line-height: 1;
  }
  .brand__tagline {
    font-size: 13.5px;
    color: var(--light-grey);
    letter-spacing: 0.2px;
  }
  .band {
    height: 76px;
    background: var(--brand-blue);
    display: flex;
    align-items: center;
    justify-content: center;
  }
  .band__label {
    color: var(--white);
    font-size: 27px;
    font-style: italic;
    font-weight: 600;
    letter-spacing: 0.3px;
  }

  /* Option 1 – grey frame */
  .sticker--grey-frame {
    left: 175px; top: 160px; width: 270px; height: 320px;
    border: 10px solid var(--frame-grey);
    border-radius: 26px;
  }
  .sticker--grey-frame .sticker__face { border-radius: 14px; }

  /* Option 2 – green edge, dark keyline */
  .sticker--green-edge {
    left: 478px; top: 160px; width: 270px; height: 320px;
    background: var(--brand-green);
    padding: 5px;
    border-radius: 24px;
  }
  .sticker--green-edge .sticker__face {
    border: 4px solid var(--dark-line);
    border-radius: 18px;
  }

  /* Option 3 – orange frame */
  .sticker--orange-frame {
    left: 778px; top: 158px; width: 272px; height: 324px;
    background: var(--brand-orange);
    padding: 10px;
    border-radius: 26px;
  }
  .sticker--orange-frame .sticker__face { border-radius: 16px; padding: 0 3px 3px; }
  .sticker--orange-frame .band { border-radius: 0 0 14px 14px; }

  /* Options 4 & 5 – tri-colour keylines */
  .sticker--tri-line,
  .sticker--tri-line-grey {
    top: 512px; width: 256px; height: 308px;
    border-radius: 18px;
    border: 3px solid var(--brand-blue);
    background: var(--white);
    box-shadow:
      0 0 0 3px var(--white),
      0 0 0 5px var(--brand-green),
      0 0 0 7px var(--white),
      0 0 0 9px var(--brand-orange);
  }
  .sticker--tri-line { left: 177px; }
  .sticker--tri-line-grey { left: 482px; }
  .sticker--tri-line .sticker__face,
  .sticker--tri-line-grey .sticker__face { border-radius: 14px; }
  .sticker--tri-line .band { height: 70px; }
  .sticker--tri-line .band__label {
    font-weight: 800;
    text-shadow: 0 0 2px var(--brand-blue-deep), 1px 1px 0 var(--brand-blue-deep);
  }
  .sticker--tri-line-grey .sticker__face { padding: 0 3px 3px; }
  .sticker--tri-line-grey .band {
    height: 68px;
    background: var(--band-grey);
    border-radius: 0 0 12px 12px;
  }

  /* Option 6 – soft orange glow, gradient band */
  .sticker--glow {
    left: 784px; top: 508px; width: 260px; height: 316px;
    border-radius: 22px;
    border: 4px solid var(--white);
    box-shadow: 0 0 6px 3px var(--brand-orange);
  }
  .sticker--glow .sticker__face { border-radius: 18px; }
  .sticker--glow .band {
    height: 72px;
    background: linear-gradient(to bottom, var(--white) 0%, #a7d6f2 35%, var(--brand-blue-deep) 100%);
  }
  .sticker--glow .band__label {
    font-weight: 800;
    color: var(--white);
    -webkit-text-stroke: 1.5px var(--ink-grey);
    font-size: 29px;
  }
</style>
</head>
<body>

  <div class="sticker sticker--grey-frame">
    <div class="sticker__face">
      <div class="brand">
        <div class="brand__mark"><span class="brand__dot"></span><span class="brand__name">Brisk Paw</span></div>
        <div class="brand__tagline">PREMIUM PET PRODUCTS</div>
      </div>
      <div class="band"><span class="band__label">DELIVERED</span></div>
    </div>
  </div>

  <div class="sticker sticker--green-edge">
    <div class="sticker__face">
      <div class="brand">
        <div class="brand__mark"><span class="brand__dot"></span><span class="brand__name">Brisk Paw</span></div>
        <div class="brand__tagline">PREMIUM PET PRODUCTS</div>
      </div>
      <div class="band"><span class="band__label">DELIVERED</span></div>
    </div>
  </div>

  <div class="sticker sticker--orange-frame">
    <div class="sticker__face">
      <div class="brand">
        <div class="brand__mark"><span class="brand__dot"></span><span class="brand__name">Brisk Paw</span></div>
        <div class="brand__tagline">PREMIUM PET PRODUCTS</div>
      </div>
      <div class="band"><span class="band__label">DELIVERED</span></div>
    </div>
  </div>

  <div class="sticker sticker--tri-line">
    <div class="sticker__face">
      <div class="brand">
        <div class="brand__mark"><span class="brand__dot"></span><span class="brand__name">Brisk Paw</span></div>
        <div class="brand__tagline">PREMIUM PET PRODUCTS</div>
      </div>
      <div class="band"><span class="band__label">DELIVERED</span></div>
    </div>
  </div>

  <div class="sticker sticker--tri-line-grey">
    <div class="sticker__face">
      <div class="brand">
        <div class="brand__mark"><span class="brand__dot"></span><span class="brand__name">Brisk Paw</span></div>
        <div class="brand__tagline">PREMIUM PET PRODUCTS</div>
      </div>
      <div class="band"><span class="band__label">DELIVERED</span></div>
    </div>
  </div>

  <div class="sticker sticker--glow">
    <div class="sticker__face">
      <div class="brand">
        <div class="brand__mark"><span class="brand__dot"></span><span class="brand__name">Brisk Paw</span></div>
        <div class="brand__tagline">PREMIUM PET PRODUCTS</div>
      </div>
      <div class="band"><span class="band__label">DELIVERED</span></div>
    </div>
  </div>

</body>
</html>
```